Young, dynamic furniture company needs a new business card design

We require a new business card design for our modern furniture company which supplies furniture and appliances to the property and development market.
Oakridge Interiors has become one of the leading furniture & appliance suppliers to the property market withing London. With over 10 years experience, we have increased our business to supply not only private landlords and managing agents, but also property developers, housing associations and local councils.
We offer not only a complete range of furniture which includes beds, wardrobes, dining sets and sofas, but also a high quality, full delivery and assembly service to help you with all our furnishing needs.

Target Market(s)

Private landlords, estate agents, letting agents, property management companies

Industry/Entity Type

Business

Contact Information for Business Card

Name,
Title,
Address,
Mobile,
Telephone,
Fax, Website, email address

Font styles to use
Sans Serif

Colors
3176b5
0555a3
85abd2
cfdeed

Requirements
Must have
• All the above information for each of our staff, along with our logo

```html
<!DOCTYPE html>
<html lang="en">
<head>
<meta charset="utf-8">
<title>Oakridge Interiors – Business Card</title>
<link href="https://fonts.googleapis.com/css2?family=Roboto:wght@400;500;700&display=swap" rel="stylesheet">
<style>
  :root {
    --blue: #3176b5;
    --navy: #0555a3;
    --deep-navy: #1f3f8a;
    --sky: #85abd2;
    --mist: #cfdeed;
    --white: #ffffff;
    --ink: #333a44;
    --grey: #7a7f88;
    --page: #e9ecf0;
  }
  * { margin: 0; padding: 0; box-sizing: border-box; }
  html, body {
    width: 1200px; height: 950px; overflow: hidden;
    background: var(--page);
    font-family: "Roboto", Arial, sans-serif;
  }
  .sheet {
    width: 1200px; height: 950px;
    display: flex; flex-direction: column; align-items: center; justify-content: center;
    gap: 30px;
  }
  .card {
    position: relative;
    width: 760px; height: 434px;
    overflow: hidden;
    box-shadow: 0 6px 18px rgba(20, 30, 50, 0.18);
  }

  /* Back side */
  .card--back {
    background: var(--blue);
    color: var(--white);
    display: flex; flex-direction: column; align-items: center; justify-content: center;
  }
  .brand { display: flex; align-items: center; gap: 14px; }
  .brand__square { width: 34px; height: 34px; background: currentColor; }
  .brand__name {
    font-size: 38px; font-weight: 500; letter-spacing: 1px; text-transform: uppercase;
  }
  .brand__tagline {
    margin-top: 8px; font-size: 15px; letter-spacing: 2px; text-transform: uppercase;
  }
  .card--back .website {
    margin-top: 46px; font-size: 20px; letter-spacing: 6px;
  }

  /* Front side */
  .card--front { background: var(--white); }
  .card__shapes { position: absolute; inset: 0; }
  .card--front .brand-block {
    position: absolute; right: 56px; top: 60px; text-align: right; color: var(--ink);
  }
  .card--front .brand { justify-content: flex-end; }
  .card--front .brand__square { background: var(--navy); width: 28px; height: 28px; }
  .card--front .brand__name { font-size: 28px; color: var(--ink); }
  .card--front .brand__tagline { font-size: 11px; color: var(--ink); }

  .person { position: absolute; left: 60px; bottom: 40px; }
  .person__name { font-size: 26px; font-weight: 700; color: var(--deep-navy); text-transform: uppercase; letter-spacing: 0.5px; }
  .person__title { font-size: 17px; color: var(--blue); text-transform: uppercase; margin-bottom: 14px; letter-spacing: 0.5px; }
  .contact-list { list-style: none; }
  .contact-list li {
    display: flex; align-items: center; gap: 12px;
    font-size: 17px; color: var(--grey); line-height: 27px;
  }
  .contact-list svg { width: 16px; height: 16px; fill: var(--deep-navy); flex: none; }

  .divider {
    position: absolute; left: 330px; bottom: 60px; width: 1px; height: 130px; background: var(--mist);
  }
  .address {
    position: absolute; left: 352px; bottom: 130px;
    font-size: 17px; color: var(--grey); line-height: 26px;
  }
  .address .website { letter-spacing: 2px; }
</style>
</head>
<body>
<main class="sheet">

  <section class="card card--back">
    <div class="brand">
      <span class="brand__square"></span>
      <span class="brand__name">Oakridge Interiors</span>
    </div>
    <p class="brand__tagline">Trade Furniture Solutions</p>
    <p class="website">www.oakridge.co</p>
  </section>

  <section class="card card--front">
    <svg class="card__shapes" viewBox="0 0 760 434" preserveAspectRatio="none" aria-hidden="true">
      <polygon points="0,0 150,0 0,115" fill="var(--deep-navy)"/>
      <polygon points="760,50 760,300 700,300" fill="var(--blue)"/>
    </svg>

    <div class="brand-block">
      <div class="brand">
        <span class="brand__square"></span>
        <span class="brand__name">Oakridge Interiors</span>
      </div>
      <p class="brand__tagline">Trade Furniture Solutions</p>
    </div>

    <div class="person">
      <h1 class="person__name">Daniel Hart</h1>
      <p class="person__title">President</p>
      <ul class="contact-list">
        <li>
          <svg viewBox="0 0 16 16"><path d="M3 1l3 3-2 2c1 2 3 4 5 5l2-2 3 3-2 3C6 15 1 10 1 3z"/></svg>
          020 7946 0182
        </li>
        <li>
          <svg viewBox="0 0 16 16"><path d="M4 0h8v16H4zM5.5 2v10h5V2z"/></svg>
          077 0090 4417
        </li>
        <li>
          <svg viewBox="0 0 16 16"><path d="M4 1h7v4H4zM1 6h14v7H12v2H4v-2H1zM5 11v3h6v-3z"/></svg>
          020 7946 0355
        </li>
        <li>
          <svg viewBox="0 0 16 16"><path d="M0 3h16v10H0zM1.5 4.5v.6L8 9l6.5-3.9v-.6z"/></svg>
          daniel@oakridge.co
        </li>
      </ul>
    </div>

    <div class="divider"></div>

    <address class="address" style="font-style: normal;">
      41 Harrow Lane<br>
      London, NW6 2QR<br>
      <span class="website">www.oakridge.co</span>
    </address>
  </section>

</main>
</body>
</html>
```